Business card for a Exhibition booth fabrication company

Hi. My company would like to change our corporate name card. We are an events and Exhibition stand builder company. We would like our corporate name card to resonate what we do. I need someone to create something unique that relates to the industry that I am in. The graphic designer should be creative to incorporate the elements of my industry and try to blend in well in the design of the card. Our aim is to ensure that we are unique and our card can look different from our competitors.
Updates

Target Market(s)

Marketing and events manager from all companies

Contact Information for Business Card

The business card should have the following details:
Name
Job Title
Email
Website

Colors

Designer to choose colors to be used in the design.

Requirements
Must have
• The card must be look something that is relevant to the service that I am providing. My website is: www.velmora-buildworks.com
• You can see my website to get more information on what service that I am doing
Nice to have
• On the back of my card, I would like to have a globe image with the incorporation of my company logo. This is to indicate that my services can be done in any part of the world.

```html
<!DOCTYPE html>
<html lang="en">
<head>
<meta charset="utf-8">
<title>Velmora Buildworks – Business Card</title>
<link href="https://fonts.googleapis.com/css2?family=Oswald:wght@500&family=Poppins:wght@400&family=Montserrat:wght@500&display=swap" rel="stylesheet">
<style>
  :root {
    --stage: #2a2a2b;
    --card-front: #ffffff;
    --card-back: #5f6062;
    --brand-red: #e3191f;
    --ink: #555557;
    --ink-soft: #6b6b6d;
    --frame-light: #e4e4e6;
    --frame-dark: #747578;
    --white: #f4f4f4;
  }
  * { margin: 0; padding: 0; box-sizing: border-box; }
  html, body { width: 1200px; height: 900px; overflow: hidden; }
  body {
    background: var(--stage);
    display: flex;
    flex-direction: column;
    align-items: center;
    justify-content: center;
    gap: 50px;
    font-family: "Poppins", sans-serif;
  }
  .card {
    width: 630px;
    height: 360px;
    border-radius: 22px;
    position: relative;
    overflow: hidden;
    box-shadow: 0 10px 30px rgba(0,0,0,0.45);
  }
  .card-front { background: var(--card-front); }
  .card-back { background: var(--card-back); }

  .stand-frame {
    position: absolute;
    inset: 0;
    width: 100%;
    height: 100%;
    pointer-events: none;
  }

  .identity {
    position: absolute;
    left: 44px;
    top: 112px;
    width: 266px;
    text-align: right;
  }
  .person-name {
    font-family: "Oswald", sans-serif;
    font-weight: 500;
    font-size: 50px;
    line-height: 1;
    color: var(--brand-red);
    text-transform: uppercase;
    letter-spacing: -0.5px;
    text-align: left;
    white-space: nowrap;
  }
  .person-title {
    font-size: 17px;
    color: var(--ink-soft);
    margin-top: 4px;
  }

  .divider {
    position: absolute;
    left: 330px;
    top: 136px;
    width: 2px;
    height: 98px;
    background: var(--brand-red);
  }

  .contact-list {
    position: absolute;
    left: 350px;
    top: 138px;
    list-style: none;
  }
  .contact-item {
    display: flex;
    align-items: center;
    gap: 8px;
    font-size: 14px;
    line-height: 24px;
    color: var(--ink);
  }
  .contact-icon { width: 12px; height: 12px; flex: none; }

  .address {
    position: absolute;
    left: 44px;
    bottom: 40px;
    font-size: 15px;
    color: var(--ink);
  }

  .brand-lockup {
    position: absolute;
    inset: 0;
    display: flex;
    flex-direction: column;
    align-items: center;
    justify-content: center;
    gap: 20px;
  }
  .globe {
    width: 120px;
    height: 120px;
    border-radius: 50%;
    background: radial-gradient(circle at 35% 30%, #f05a5e 0%, var(--brand-red) 55%, #a70f14 100%);
  }
  .brand-name {
    font-family: "Montserrat", sans-serif;
    font-weight: 500;
    font-size: 30px;
    letter-spacing: 4px;
    color: var(--white);
    text-transform: uppercase;
  }
</style>
</head>
<body>

<section class="card card-front">
  <svg class="stand-frame" viewBox="0 0 630 360" aria-hidden="true">
    <g fill="none" stroke="var(--frame-light)" stroke-width="2">
      <path d="M470 0 V70 H630"/>
      <path d="M500 0 V40 H630"/>
      <path d="M470 70 L500 40"/>
      <path d="M560 0 V70"/>
    </g>
    <rect x="0" y="350" width="630" height="10" fill="var(--brand-red)"/>
  </svg>

  <div class="identity">
    <h1 class="person-name">Daniel Hart</h1>
    <p class="person-title">Director</p>
  </div>

  <span class="divider"></span>

  <ul class="contact-list">
    <li class="contact-item">
      <svg class="contact-icon" viewBox="0 0 12 12"><path d="M2.5 1 L4.5 1 L5 3.5 L3.8 4.4 Q5 7 7.6 8.2 L8.5 7 L11 7.5 L11 9.5 Q11 11 9.5 11 Q1 10 1 2.5 Q1 1 2.5 1 Z" fill="var(--brand-red)"/></svg>
      +65 81550142
    </li>
    <li class="contact-item">
      <svg class="contact-icon" viewBox="0 0 12 12"><rect x="3" y="0.8" width="6" height="10.4" rx="1.2" fill="none" stroke="var(--brand-red)" stroke-width="1.4"/><circle cx="6" cy="9.2" r="0.7" fill="var(--brand-red)"/></svg>
      +974 55120478
    </li>
    <li class="contact-item">
      <svg class="contact-icon" viewBox="0 0 12 12"><rect x="0.8" y="2.3" width="10.4" height="7.4" rx="1" fill="none" stroke="var(--brand-red)" stroke-width="1.3"/><path d="M1 2.8 L6 6.6 L11 2.8" fill="none" stroke="var(--brand-red)" stroke-width="1.3"/></svg>
      info@velmora-buildworks.com
    </li>
    <li class="contact-item">
      <svg class="contact-icon" viewBox="0 0 12 12"><circle cx="6" cy="6" r="5" fill="none" stroke="var(--brand-red)" stroke-width="1.2"/><ellipse cx="6" cy="6" rx="2.2" ry="5" fill="none" stroke="var(--brand-red)" stroke-width="1"/><path d="M1 6 H11 M1.8 3.5 H10.2 M1.8 8.5 H10.2" stroke="var(--brand-red)" stroke-width="0.9"/></svg>
      www.velmora-buildworks.com
    </li>
  </ul>

  <p class="address">P.O. Box 3182 Marina Row Street Doha - Qatar</p>
</section>

<section class="card card-back">
  <svg class="stand-frame" viewBox="0 0 630 360" aria-hidden="true">
    <g fill="none" stroke="var(--frame-dark)" stroke-width="2">
      <path d="M40 320 V40 H590 V320"/>
      <path d="M40 40 L80 70 H550 L590 40"/>
      <path d="M80 70 V320 M550 70 V320"/>
      <path d="M20 320 H610"/>
    </g>
  </svg>
  <div class="brand-lockup">
    <span class="globe" role="img" aria-label="Globe showing worldwide exhibition stand service"></span>
    <span class="brand-name">Velmora Buildworks</span>
  </div>
</section>

</body>
</html>
```